redesign of my existing custom website into Wordpress based website

I need someone to redesign my current website into something more classy, simplistic, modern and on trend. I would like it set up on Wordpress in a way thats easy for me to make my own additions to blogs/price changes and promotion banners. I will also need a page that is password protected so members can login and have access to all my training videos and resources.
website is www.tidewellmamas.com.au

Target Market(s)

new mums

Industry/Entity Type

Fitness

Coding

Coded - Design and coding required

Number of Pages Required

5+ page

Colors
33a6d7

Requirements
Must have
• chic, modern, stylish and simplistic.
• a call to action above the page fold
• mobile friendly conversion
• a pop up message as soon as someone enters my sight offering my free report
• a members page that is password protected containing 3 youtube videos and 6 pdf attachments as resources
• a home page
• a contact us page
• an about us page
• a blog page
• a store page
Nice to have
• some examples of my peers websites that I like:
• www.norapellwick.com
• https://www.9qlr.com
• https://41bytedgarth.com
Should not have
• anything gimmicky

```html
<!DOCTYPE html>
<html lang="en">
<head>
<meta charset="utf-8">
<title>Larkfield Mums – 12 Week Home Workout Program</title>
<link href="https://fonts.googleapis.com/css2?family=Oswald:wght@300;400;500&family=Open+Sans:wght@400;600;700&display=swap" rel="stylesheet">
<style>
:root{
  --brand:#33a6d7;
  --brand-dark:#2a8fbb;
  --ink:#3a3a3a;
  --muted:#8a8a8a;
  --line:#e4e4e4;
  --paper:#ffffff;
  --soft:#f6f6f6;
  --hero:#4b4b4d;
  --footer:#2f2f31;
  --logo-ink:#b7334f;
  --shade:rgba(12,12,14,.64);
}
*{box-sizing:border-box;margin:0;padding:0}
html,body{width:1200px;height:3830px;overflow:hidden}
body{font-family:"Open Sans",Arial,sans-serif;color:var(--ink);background:var(--paper);position:relative}
.abs{position:absolute}
.heading{font-family:"Oswald","Arial Narrow",sans-serif;font-weight:400}

/* hero */
.hero{left:0;top:0;width:1200px;height:633px;background:var(--hero)}
.hero-photo{left:0;top:0;width:1200px;height:633px;background:linear-gradient(90deg,#3f3f41 0%,#4a4a4c 55%,#6a625c 78%,#4e4a48 100%)}
.logo{left:133px;top:-20px;width:178px;height:178px;border-radius:50%;background:#fff;display:flex;align-items:center;justify-content:center;text-align:center;font-family:"Oswald",sans-serif;font-weight:400;font-size:22px;color:var(--logo-ink);line-height:1.15;padding-top:18px}
.nav{top:30px;left:400px;display:flex;font-size:15px;color:#fff}
.nav a{color:#fff;text-decoration:none;display:block;padding:8px 18px;margin-right:10px}
.nav a.current{border:1px solid #fff}
.cart{display:flex;align-items:center;gap:8px}
.hero-title{left:133px;top:245px;font-size:44px;line-height:56px;color:#fff}
.btn-outline{display:inline-block;border:1px solid #fff;color:#fff;font-family:"Oswald",sans-serif;font-size:14px;letter-spacing:.5px;padding:12px 26px}
.hero-btn{left:133px;top:395px}
.hero-sub{left:133px;top:470px;font-size:28px;line-height:36px;color:#8fcbe6;font-family:"Oswald",sans-serif;font-weight:300}
.dots{left:1157px;top:318px;display:flex;flex-direction:column;gap:8px}
.dots span{width:10px;height:10px;border-radius:50%;background:#aaa}
.dots span.on{background:#fff}

/* features */
.features{left:0;top:633px;width:1200px;height:547px;background:var(--paper)}
.card{top:125px;width:291px;height:330px;background:#fff;border:1px solid var(--line)}
.card-photo{width:100%;height:174px}
.card h3{font-family:"Oswald",sans-serif;font-weight:400;font-size:15px;text-align:center;margin:30px 12px 10px;color:var(--ink)}
.card p{font-size:12px;line-height:18px;color:var(--muted);text-align:center;padding:0 16px}
.card .more{position:absolute;left:50%;bottom:-22px;margin-left:-22px;width:44px;height:44px;border-radius:50%;background:var(--brand)}

/* lead */
.lead{left:0;top:1180px;width:1200px;height:569px;background:linear-gradient(90deg,#d8d2c8 0%,#ece8e2 45%,#f3f1ee 100%)}
.lead-box{left:735px;top:79px;width:332px;height:395px;background:#fff;padding:34px 28px}
.lead-box h3{color:var(--brand);text-align:center;font-size:24px;line-height:32px;font-family:"Oswald",sans-serif;font-weight:400}
.lead-box p{font-size:12px;line-height:18px;text-align:center;color:var(--muted);margin:16px 0 18px}
.lead-box p b{color:var(--brand)}
.field{height:40px;border-bottom:1px solid var(--line);font-size:12px;color:var(--muted);display:flex;align-items:center;padding-left:10px}
.btn-solid{display:block;background:var(--brand);color:#fff;text-align:center;font-family:"Oswald",sans-serif;font-size:14px;padding:12px 0}
.lead-box .btn-solid{margin-top:18px}

/* packs */
.pack{left:0;width:1200px;height:352px}
.pack-text{top:0;width:602px;height:352px;background:#fff;padding:58px 0 0 130px}
.pack-text h3{color:var(--brand);font-size:22px;font-family:"Oswald",sans-serif;font-weight:400;margin-bottom:18px}
.pack ul{list-style:none}
.pack li{font-size:13px;line-height:25px;display:flex;align-items:center;gap:10px}
.pack .price{font-weight:700;font-size:15px;margin-top:14px;padding-left:14px}

/* band */
.band{left:0;top:2451px;width:1200px;height:413px;background:var(--brand)}
.band-small{left:133px;top:88px;color:#fff;font-family:"Oswald",sans-serif;font-weight:300;font-size:16px}
.band-title{left:133px;top:112px;color:#fff;font-size:34px;font-family:"Oswald",sans-serif;font-weight:400}
.band-copy{left:133px;top:170px;width:620px;color:#eaf6fb;font-size:13px;line-height:21px}
.band-btn{left:133px;top:278px}
.band-art{left:779px;top:89px;width:288px;height:256px;background:linear-gradient(135deg,#5b7b8a,#a7527a 55%,#d6c6b5)}

/* news */
.news{left:0;top:2864px;width:1200px;height:506px;background:#fff}
.news h2{position:absolute;top:58px;width:100%;text-align:center;font-size:26px;font-family:"Oswald",sans-serif;font-weight:400}
.post{top:138px;width:217px;height:304px;border:1px solid var(--line);background:#fff}
.post-photo{height:108px}
.post-body{padding:16px 14px}
.post .date{font-size:11px;color:var(--muted)}
.post h4{font-size:14px;font-weight:600;margin:14px 0 10px}
.post p{font-size:11px;line-height:17px;color:var(--muted)}
.post .read{font-family:"Oswald",sans-serif;font-size:12px;color:var(--brand);margin-top:12px;display:block}

/* cta */
.cta{left:0;top:3370px;width:1200px;height:281px;background:#f4f4f4;text-align:center}
.cta h2{font-size:24px;font-family:"Oswald",sans-serif;font-weight:400;margin-top:96px}
.cta p{font-size:20px;font-family:"Oswald",sans-serif;color:var(--ink);margin-top:8px;font-weight:300}
.cta .btn-solid{display:inline-block;padding:12px 28px;margin-top:20px}

/* footer */
.footer{left:0;top:3651px;width:1200px;height:179px;background:var(--footer);color:#bbb}
.foot-links{left:133px;top:42px;display:flex;gap:22px;font-size:12px;color:#ddd}
.foot-copy{left:133px;top:72px;width:680px;font-size:11px;line-height:18px;color:#999}
.foot-logo{left:958px;top:36px;width:120px;text-align:center;font-family:"Oswald",sans-serif;font-weight:400;font-size:13px;color:#ccc;display:flex;flex-direction:column;align-items:center;gap:6px}
.foot-logo span{width:44px;height:44px;border-radius:50%;border:1px solid #888}
.social{left:1000px;top:128px;display:flex;gap:10px}
.social span{width:26px;height:26px;border-radius:50%;border:1px solid #888}

/* shade + modal */
.shade{left:0;top:0;width:1200px;height:3830px;background:var(--shade)}
.modal{left:311px;top:324px;width:634px;height:434px;background:#fff;padding:0 40px}
.modal h2{text-align:center;font-size:34px;font-family:"Oswald",sans-serif;font-weight:500;margin-top:26px;color:#222}
.modal p{text-align:center;font-size:11.5px;line-height:18px;color:#555;margin:14px 0 0}
.report{left:60px;top:187px;width:153px;height:179px;background:linear-gradient(160deg,#e33c8b,#b52a6e 60%,#f4f4f4 60%);border:1px solid #ddd}
.modal .input{position:absolute;left:245px;width:343px;height:38px;border:1px solid #dcdcdc;font-size:12px;color:#555;display:flex;align-items:center;gap:8px;padding-left:12px}
.modal .btn-solid{position:absolute;left:245px;top:345px;width:128px;font-size:13px;padding:10px 0}
.close{left:897px;top:261px;width:70px;height:70px;border-radius:50%;background:var(--brand);border:4px solid #fff;color:#fff;font-family:"Open Sans",sans-serif;font-size:18px;display:flex;align-items:center;justify-content:center}
</style>
</head>
<body>

<header class="hero abs">
  <div class="hero-photo abs" role="img" aria-label="Smiling woman in workout clothes standing on the right against a dark background"></div>
  <div class="logo abs">Larkfield<br>Mums</div>
  <nav class="nav abs">
    <a class="current">Home</a><a>About Us</a><a>Program</a><a>Blog</a><a>Shop</a><a>Contact</a>
    <a class="cart">My cart
      <svg width="20" height="18" viewBox="0 0 20 18"><path d="M1 2h3l2 10h10l2-7H6" fill="none" stroke="#fff" stroke-width="1.5"/><circle cx="8" cy="15" r="1.5" fill="#fff"/><circle cx="15" cy="15" r="1.5" fill="#fff"/><circle cx="17" cy="3" r="3" fill="#33a6d7"/></svg>
    </a>
  </nav>
  <h1 class="hero-title abs heading">12 Week Home Workout<br>Program For Mums</h1>
  <a class="btn-outline hero-btn abs">GET STARTED NOW</a>
  <p class="hero-sub abs">Start seeing results from home<br>in just a few weeks</p>
  <div class="dots abs"><span class="on"></span><span></span><span></span></div>
</header>

<section class="features abs">
  <article class="card abs" style="left:133px">
    <div class="card-photo" role="img" aria-label="Mother exercising on a mat beside her baby" style="background:linear-gradient(135deg,#b99c8e,#d7c2b5)"></div>
    <h3>SPECIALLY DESIGNED FOR MUMS</h3>
    <p>Short home sessions built around nap times so busy mums can train safely and see steady progress week by week.</p>
    <span class="more"></span>
  </article>
  <article class="card abs" style="left:454px">
    <div class="card-photo" role="img" aria-label="Home workout equipment with a toddler playing nearby" style="background:linear-gradient(135deg,#8a8f92,#c7b8a8)"></div>
    <h3>WORKOUT EQUIPMENT</h3>
    <p>Everything you need arrives at your door, including bands, weights and a mat chosen for simple daily workouts.</p>
    <span class="more"></span>
  </article>
  <article class="card abs" style="left:779px">
    <div class="card-photo" role="img" aria-label="Mother cooking a healthy meal with her child" style="background:linear-gradient(135deg,#9d8a80,#d9c8ba)"></div>
    <h3>DELICIOUS LOW FAT FAMILY MEALS</h3>
    <p>Easy recipes the whole family will enjoy, with a weekly plan and shopping list to keep healthy eating simple.</p>
    <span class="more"></span>
  </article>
</section>

<section class="lead abs">
  <div class="abs" role="img" aria-label="Mother lifting dumbbells in a bright living room while her toddler plays" style="left:0;top:0;width:700px;height:569px;background:linear-gradient(90deg,#c9bfb2,#e2dbd2)"></div>
  <div class="lead-box abs">
    <h3>GET YOUR FREE TOP 10<br>BABY BELLY BLASTING TIPS</h3>
    <p>Sign up today and get our proven tips for a flatter tummy sent to your inbox <b>FREE TODAY!</b></p>
    <div class="field">Name</div>
    <div class="field">Email</div>
    <div class="field">Phone</div>
    <a class="btn-solid">GET IT FREE NOW</a>
  </div>
</section>

<section class="pack abs" style="top:1749px">
  <div class="pack-text abs" style="left:0">
    <h3>12 week Home Workout Program - Equipment Pack</h3>
    <ul>
      <li><svg width="12" height="12"><path d="M1 6l3 3 7-7" stroke="#3a3a3a" stroke-width="1.6" fill="none"/></svg>Our unique 3 stage, 12 week training program</li>
      <li><svg width="12" height="12"><path d="M1 6l3 3 7-7" stroke="#3a3a3a" stroke-width="1.6" fill="none"/></svg>Full instructional workout DVD and program guide for each program</li>
      <li><svg width="12" height="12"><path d="M1 6l3 3 7-7" stroke="#3a3a3a" stroke-width="1.6" fill="none"/></svg>Weekly accountability check</li>
      <li><svg width="12" height="12"><path d="M1 6l3 3 7-7" stroke="#3a3a3a" stroke-width="1.6" fill="none"/></svg>Weekly coaching emails</li>
      <li><svg width="12" height="12"><path d="M1 6l3 3 7-7" stroke="#3a3a3a" stroke-width="1.6" fill="none"/></svg>Home exercise equipment for your home</li>
      <li><svg width="12" height="12"><path d="M1 6l3 3 7-7" stroke="#3a3a3a" stroke-width="1.6" fill="none"/></svg>Nutritionist approved healthy eating guide</li>
    </ul>
    <p class="price">That's only $18.50 per week!</p>
  </div>
  <div class="abs" role="img" aria-label="Close-up of a woman kneeling with red and blue hand weights" style="left:602px;top:0;width:598px;height:352px;background:linear-gradient(135deg,#2c2c2c,#6b5a52 60%,#a33a3a)"></div>
</section>

<section class="pack abs" style="top:2101px">
  <div class="abs" role="img" aria-label="Woman sitting on an exercise mat in front of a leather sofa" style="left:0;top:0;width:602px;height:350px;background:linear-gradient(135deg,#4a3c36,#8c7a6c 55%,#6a4c6e)"></div>
  <div class="pack-text abs" style="left:602px;padding-left:34px">
    <h3>12 week Home Workout Program - Basic Pack</h3>
    <ul>
      <li><svg width="12" height="12"><path d="M1 6l3 3 7-7" stroke="#3a3a3a" stroke-width="1.6" fill="none"/></svg>Our unique 3 stage, 12 week training program</li>
      <li><svg width="12" height="12"><path d="M1 6l3 3 7-7" stroke="#3a3a3a" stroke-width="1.6" fill="none"/></svg>Full instructional workout DVD for each program</li>
      <li><svg width="12" height="12"><path d="M1 6l3 3 7-7" stroke="#3a3a3a" stroke-width="1.6" fill="none"/></svg>Weekly accountability check</li>
      <li><svg width="12" height="12"><path d="M1 6l3 3 7-7" stroke="#3a3a3a" stroke-width="1.6" fill="none"/></svg>Weekly coaching emails</li>
      <li><svg width="12" height="12"><path d="M1 6l3 3 7-7" stroke="#3a3a3a" stroke-width="1.6" fill="none"/></svg>Nutritionist approved healthy eating guidance</li>
      <li><svg width="12" height="12"><path d="M1 6l3 3 7-7" stroke="#3a3a3a" stroke-width="1.6" fill="none"/></svg>Healthy family recipe cookbook ebook</li>
    </ul>
    <p class="price">That's only $7.25 per week!</p>
  </div>
</section>

<section class="band abs">
  <p class="band-small abs">Starting from only $7.50 per week</p>
  <h2 class="band-title abs">Already have the equipment you need?</h2>
  <p class="band-copy abs">Choose the basic pack and follow the same proven twelve week plan with your own gear at home. You still get every workout video, the program guide, weekly check-ins and coaching emails, plus our healthy eating guide and family recipes to keep you on track.</p>
  <a class="btn-outline band-btn abs">GET STARTED NOW</a>
  <div class="band-art abs" role="img" aria-label="Stack of program guides and recipe books with a free bonus badge"></div>
</section>

<section class="news abs">
  <h2>LATEST NEWS</h2>
  <article class="post abs" style="left:133px">
    <div class="post-photo" role="img" aria-label="Mother training with her baby" style="background:linear-gradient(135deg,#b79c8c,#d8c3b6)"></div>
    <div class="post-body"><span class="date">Jan 02, 2017</span><h4>The Benefits of Training</h4><p>Why regular movement helps new mums feel stronger and sleep better.</p><span class="read">READ MORE</span></div>
  </article>
  <article class="post abs" style="left:373px">
    <div class="post-photo" role="img" aria-label="Bowl of pumpkin soup" style="background:linear-gradient(135deg,#6d6a5e,#d9a441)"></div>
    <div class="post-body"><span class="date">Jan 02, 2017</span><h4>Creamy Pumpkin Soup</h4><p>A warming low fat recipe the whole family will ask for again.</p><span class="read">READ MORE</span></div>
  </article>
  <article class="post abs" style="left:613px">
    <div class="post-photo" role="img" aria-label="Cardio equipment on a living room floor" style="background:linear-gradient(135deg,#8c8a8e,#c6a1a6)"></div>
    <div class="post-body"><span class="date">Jan 02, 2017</span><h4>Cardio workout</h4><p>A quick twenty minute routine you can do while baby naps.</p><span class="read">READ MORE</span></div>
  </article>
  <article class="post abs" style="left:853px">
    <div class="post-photo" role="img" aria-label="Mother stretching with her toddler" style="background:linear-gradient(135deg,#a48a84,#d5c0bc)"></div>
    <div class="post-body"><span class="date">Jan 02, 2017</span><h4>Marisa's on exercise</h4><p>Our members share how small daily habits made a big difference.</p><span class="read">READ MORE</span></div>
  </article>
</section>

<section class="cta abs">
  <h2>TAKE THE FIRST STEP TODAY BY JOINING OUR PROGRAM</h2>
  <p>and let us help you bounce back to the body that you deserve!</p>
  <a class="btn-solid">GET STARTED NOW</a>
</section>

<footer class="footer abs">
  <div class="foot-links abs"><span>Home</span><span>About Us</span><span>Program</span><span>Blog</span><span>Shop</span><span>Contact</span><span>Member Portal</span></div>
  <p class="foot-copy abs">Always consult your doctor before starting any exercise program after pregnancy or birth.<br>Results vary between individuals and depend on effort, diet and lifestyle factors.<br>Copyright © 2017 Larkfield Mums. All rights reserved.</p>
  <div class="foot-logo abs"><span></span>Larkfield Mums</div>
  <div class="social abs"><span></span><span></span><span></span><span></span></div>
</footer>

<div class="shade abs"></div>

<div class="modal abs" role="dialog" aria-label="Free report offer">
  <h2>MY FREE REPORT</h2>
  <p>Download our free guide to getting back in shape after baby, with simple home workouts, meal ideas and tips from real mums who have done it, sent straight to your inbox today.</p>
  <div class="report abs" role="img" aria-label="Cover of the free report booklet"></div>
  <div class="input" style="top:194px">
    <svg width="12" height="12" viewBox="0 0 12 12"><circle cx="6" cy="4" r="2.5" fill="#999"/><path d="M1 12c0-3 2-4.5 5-4.5s5 1.5 5 4.5" fill="#999"/></svg>Username:</div>
  <div class="input" style="top:242px">
    <svg width="12" height="12" viewBox="0 0 12 12"><path d="M2 1l2 0 1 3-1.5 1c.7 1.5 1.8 2.6 3.5 3.5l1-1.5 3 1v2c0 .6-.5 1-1 1C5 11 1 7 1 2c0-.5.4-1 1-1z" fill="#999"/></svg>Phone:</div>
  <div class="input" style="top:291px">
    <svg width="12" height="12" viewBox="0 0 12 12"><rect x="1" y="2.5" width="10" height="7" fill="none" stroke="#999"/><path d="M1 3l5 4 5-4" fill="none" stroke="#999"/></svg>Email:</div>
  <a class="btn-solid">FREE REPORT</a>
</div>
<div class="close abs">X</div>

</body>
</html>
```